Real Estate Business Card

On the front side I want to have my info, my brokerage info.
On the back side I want have my complany’s logo, website and Facebook link. I will provide all this once I select a design.

I would like to see Black background and gold text, Dark Blue and gold text and White and blue text designs

Font styles to use
Sans Serif
Script

```html
<!DOCTYPE html>
<html lang="en">
<head>
<meta charset="utf-8">
<title>Harborline Realty – Business Card</title>
<link rel="stylesheet" href="https://fonts.googleapis.com/css2?family=Cinzel:wght@600&family=Open+Sans:wght@400;600&display=swap">
<style>
  :root {
    --stage: #2b2b2d;
    --navy: #12365e;
    --navy-deep: #0f2f53;
    --gold: #e9bd2a;
    --white: #f4f6f9;
    --hairline: rgba(233, 189, 42, 0.35);
  }
  * { box-sizing: border-box; margin: 0; padding: 0; }
  html, body { width: 1200px; height: 782px; overflow: hidden; background: var(--stage); }
  .canvas {
    width: 1200px; height: 782px;
    display: flex; flex-direction: column; align-items: center; justify-content: center; gap: 28px;
  }
  .card {
    position: relative;
    width: 620px; height: 354px;
    background: linear-gradient(160deg, var(--navy) 0%, var(--navy-deep) 100%);
    color: var(--white);
    font-family: "Open Sans", Arial, sans-serif;
    box-shadow: 0 10px 24px rgba(0,0,0,.45);
    overflow: hidden;
  }
  .brand {
    font-family: "Cinzel", "Times New Roman", serif;
    font-weight: 600;
    color: var(--gold);
    letter-spacing: 2px;
    white-space: nowrap;
    display: flex; align-items: center; gap: 10px;
  }
  .brand-dot { width: 9px; height: 9px; background: var(--gold); flex: none; }

  /* back side */
  .card--back .brand { position: absolute; left: 50%; top: 130px; transform: translateX(-50%); font-size: 38px; }
  .card--back .social-link {
    position: absolute; left: 0; right: 0; top: 218px; text-align: center;
    font-size: 15px; letter-spacing: .5px;
  }

  /* front side */
  .contact { position: absolute; left: 30px; top: 118px; width: 240px; }
  .contact-name {
    font-family: "Cinzel", "Times New Roman", serif; font-weight: 600;
    color: var(--gold); font-size: 20px; letter-spacing: 1.2px; line-height: 1; white-space: nowrap;
  }
  .contact-role { font-size: 14px; margin: 5px 0 10px; }
  .contact-list { list-style: none; font-size: 14px; line-height: 21px; }
  .contact-list li { display: flex; align-items: center; gap: 8px; white-space: nowrap; }
  .contact-list svg { width: 11px; height: 11px; fill: var(--gold); flex: none; }
  .divider { position: absolute; left: 275px; right: 30px; top: 168px; height: 1px; background: var(--hairline); }
  .card--front .brand { position: absolute; left: 300px; width: 290px; top: 100px; justify-content: center; font-size: 22px; letter-spacing: 1.5px; }
  .office { position: absolute; left: 340px; top: 210px; width: 250px; }
  .office-web { color: var(--gold); font-size: 16px; letter-spacing: .5px; margin-bottom: 12px; }
  .office-address { font-size: 16px; line-height: 21px; }
</style>
</head>
<body>
<main class="canvas">
  <section class="card card--back" aria-label="Card back">
    <div class="brand"><span class="brand-dot"></span>HARBORLINE REALTY</div>
    <p class="social-link">WWW.HARBORLINE.TEST/COMMUNITY</p>
  </section>

  <section class="card card--front" aria-label="Card front">
    <div class="contact">
      <p class="contact-name">DELANEY MORROW</p>
      <p class="contact-role">Managing Director</p>
      <ul class="contact-list">
        <li><svg viewBox="0 0 12 12"><path d="M2 1h3l1 3-2 1a7 7 0 0 0 3 3l1-2 3 1v3c0 1-1 1-1 1A10 10 0 0 1 1 2s0-1 1-1z"/></svg>055-210 478 316</li>
        <li><svg viewBox="0 0 12 12"><path d="M3 0h6a1 1 0 0 1 1 1v10a1 1 0 0 1-1 1H3a1 1 0 0 1-1-1V1a1 1 0 0 1 1-1zm0 2v7h6V2zm3 8.2a.7.7 0 1 0 0 1.4.7.7 0 0 0 0-1.4z"/></svg>055-210 478 317</li>
        <li><svg viewBox="0 0 12 12"><path d="M0 2h12v8H0zm1 1v.4l5 3.3 5-3.3V3zm0 1.6V9h10V4.6L6 8z"/></svg>hello@harborline.test</li>
        <li><svg viewBox="0 0 12 12"><path d="M6 0a6 6 0 1 0 0 12A6 6 0 0 0 6 0zm0 1c.8 0 1.6 1.6 1.9 4H4.1C4.4 2.6 5.2 1 6 1zM1 6.5h2.1c0 1.5.3 2.8.8 3.8A5 5 0 0 1 1 6.5zm0-1a5 5 0 0 1 2.9-3.8c-.5 1-.8 2.3-.8 3.8zm5 5.5c-.8 0-1.6-1.6-1.9-4.5h3.8C7.6 9.4 6.8 11 6 11zm2.1-.7c.5-1 .8-2.3.8-3.8H11a5 5 0 0 1-2.9 3.8zM8.9 5.5c0-1.5-.3-2.8-.8-3.8A5 5 0 0 1 11 5.5z"/></svg>www.harborline.test</li>
      </ul>
    </div>
    <div class="divider"></div>
    <div class="brand"><span class="brand-dot"></span>HARBORLINE REALTY</div>
    <div class="office">
      <p class="office-web">www.harborline.test</p>
      <p class="office-address">48 Quayside Lane, Suite 9<br>Port Aldery, 204518</p>
    </div>
  </section>
</main>
</body>
</html>
```